SkyvornQ Business Cards and Stationary Design

Need a design for our business cards and stationary. I want to carry on the theme of the logo. I want the business cards to have a design on the back. I would like the business cards and the stationary to carry the same theme, design scheme, and branding

Target Market(s)

Airlines and Maintenance Facilities

Industry/Entity Type

Aviation

Contact Information for Business Card

Name
Position Title
Address: 4827 Trellis Hollow Road, Alder Cove, Marivale, 34951
Office Number
Mobile Number
Email
Website

Font styles to use
Serif
Sans Serif

Colors

Designer to choose colors to be used in the design.

```html
<!DOCTYPE html>
<html lang="en">
<head>
<meta charset="UTF-8">
<title>SkyvornQ Business Card</title>
<link href="https://fonts.googleapis.com/css2?family=Oswald:wght@600&family=Work+Sans:wght@400;600&display=swap" rel="stylesheet">
<style>
  :root {
    --navy: #142a56;
    --navy-deep: #0f2148;
    --ink: #1b2c55;
    --text-grey: #4a4f5a;
    --silver: #c9ced8;
    --paper: #ffffff;
    --paper-shade: #eef0f3;
    --watermark: #e6eaf1;
    --stage: #d9dce1;
  }
  * { margin: 0; padding: 0; box-sizing: border-box; }
  html, body {
    width: 1200px;
    height: 900px;
    overflow: hidden;
    background: var(--stage);
  }
  .sheet {
    width: 1200px;
    height: 900px;
    display: flex;
    flex-direction: column;
    align-items: center;
    justify-content: center;
    gap: 40px;
  }
  .card {
    width: 700px;
    height: 400px;
    border-radius: 22px;
    position: relative;
    overflow: hidden;
    box-shadow: 0 10px 28px rgba(0, 0, 0, 0.25);
  }

  /* Front */
  .card-front {
    background: linear-gradient(160deg, var(--paper-shade) 0%, var(--paper) 55%);
    font-family: "Work Sans", Arial, sans-serif;
  }
  .front-ring {
    position: absolute;
    left: 250px;
    top: 70px;
    width: 240px;
    height: 240px;
    border: 16px solid var(--watermark);
    border-radius: 50%;
  }
  .identity {
    position: absolute;
    left: 120px;
    top: 118px;
    text-align: right;
    width: 270px;
  }
  .person-name {
    font-family: "Oswald", "Arial Narrow", sans-serif;
    font-weight: 600;
    font-size: 44px;
    letter-spacing: 1px;
    color: var(--ink);
    text-transform: uppercase;
    line-height: 1;
  }
  .person-role {
    font-size: 17px;
    color: var(--text-grey);
    margin-top: 6px;
  }
  .divider {
    position: absolute;
    left: 410px;
    top: 128px;
    width: 2px;
    height: 86px;
    background: var(--ink);
  }
  .contact-list {
    position: absolute;
    left: 432px;
    top: 134px;
    list-style: none;
  }
  .contact-list li {
    display: flex;
    align-items: center;
    gap: 10px;
    font-size: 19px;
    color: var(--text-grey);
    line-height: 1.4;
  }
  .contact-list svg { width: 14px; height: 14px; flex: none; }
  .contact-list strong { color: var(--ink); font-weight: 600; }
  .address {
    position: absolute;
    left: 0;
    right: 0;
    bottom: 58px;
    text-align: center;
    font-size: 19px;
    color: var(--text-grey);
  }

  /* Back */
  .card-back {
    background: linear-gradient(160deg, var(--navy) 0%, var(--navy-deep) 100%);
    font-family: "Work Sans", Arial, sans-serif;
    display: flex;
    flex-direction: column;
    align-items: center;
    justify-content: center;
  }
  .brand-mark {
    width: 90px;
    height: 90px;
    border: 9px solid var(--silver);
    border-radius: 50%;
    margin-bottom: 22px;
  }
  .brand-name {
    font-weight: 600;
    font-size: 64px;
    letter-spacing: 10px;
    color: var(--silver);
    text-transform: uppercase;
    line-height: 1;
  }
  .brand-site {
    margin-top: 26px;
    font-size: 20px;
    color: var(--silver);
    letter-spacing: 0.5px;
  }
</style>
</head>
<body>
<main class="sheet">
  <section class="card card-front" aria-label="Business card front">
    <div class="front-ring" aria-hidden="true"></div>
    <div class="identity">
      <h1 class="person-name">Dorian Vale</h1>
      <p class="person-role">Director</p>
    </div>
    <div class="divider" aria-hidden="true"></div>
    <ul class="contact-list">
      <li>
        <svg viewBox="0 0 16 16" aria-hidden="true"><path d="M4 1.5l2.2 3-1.4 1.6c.9 2 2.3 3.4 4.1 4.2l1.6-1.4 3 2.2-1.2 2.6C7 13.6 2.4 9 1.5 3.2z" fill="#1b2c55"/></svg>
        555-270-3918
      </li>
      <li>
        <svg viewBox="0 0 16 16" aria-hidden="true"><rect x="1.5" y="3.5" width="13" height="9" rx="1" fill="none" stroke="#1b2c55" stroke-width="1.6"/><path d="M2 4l6 5 6-5" fill="none" stroke="#1b2c55" stroke-width="1.6"/></svg>
        info@skyvornq.com
      </li>
      <li>
        <svg viewBox="0 0 16 16" aria-hidden="true"><circle cx="8" cy="8" r="6.5" fill="none" stroke="#1b2c55" stroke-width="1.4"/><ellipse cx="8" cy="8" rx="2.8" ry="6.5" fill="none" stroke="#1b2c55" stroke-width="1.2"/><path d="M1.5 8h13" stroke="#1b2c55" stroke-width="1.2"/></svg>
        <span>www.<strong>skyvornq</strong>.com</span>
      </li>
    </ul>
    <p class="address">4827 Trellis Hollow Road, Alder Cove, Marivale, 34951</p>
  </section>

  <section class="card card-back" aria-label="Business card back">
    <div class="brand-mark" aria-hidden="true"></div>
    <p class="brand-name">SkyvornQ</p>
    <p class="brand-site">www.skyvornq.com</p>
  </section>
</main>
</body>
</html>
```